Business card for marketing analytics company

Need a business card for new company. I have a logo already that I want to be built into the card and should use those colours

Company is called steered by tallies
Design must bring steered by tallies to life not be a card that could be for anyone with a logo put on it.

Like the front to be fairly clean and uncluttered bringing the logo out with a suitable design on the back of the card.

The logo represents a compass and business growth so those themes along with numbers, analytics , data are appropriate.
I'm often working with creative industries so also needs to reflect the creative side of analytics rather than be very corporate looking.

Target Market(s)

Ad agency, media agency, consumer goods clients

Industry/Entity Type

Market Research

Contact Information for Business Card

Needs to include name, title, email and phone number

Colors
f78f20
f68d4d
ec1f27

Requirements
Must have
• Must bring steered by tallies to life not be a card that could be for anyone with a logo put on it.
• Logo, Correct colours
• Like a design on the back that relates to company name
• Designs for both sides
Should not have
• Please do not just submit logo and a coloured card.
• It needs to have a design element to it
• No black background
• No clear cards - needs front & back

```html
<!DOCTYPE html>
<html lang="en">
<head>
<meta charset="utf-8">
<title>Steered by Tallies – Business Cards</title>
<link rel="stylesheet" href="https://fonts.googleapis.com/css2?family=Montserrat:wght@500;600;700&family=Open+Sans:wght@400;600&display=swap">
<style>
  :root {
    --orange: #f47a20;
    --orange-soft: #f78f20;
    --red: #e4202a;
    --slate: #4d5963;
    --grey-text: #555c63;
    --card: #ffffff;
    --backdrop: #e9eaec;
  }
  * { margin: 0; padding: 0; box-sizing: border-box; }
  html, body { width: 1200px; height: 1000px; overflow: hidden; }
  body {
    background: var(--backdrop);
    position: relative;
    font-family: "Open Sans", Arial, sans-serif;
  }
  .card {
    position: absolute;
    width: 600px;
    height: 340px;
    background: var(--card);
    border-radius: 26px;
    overflow: hidden;
    box-shadow: 0 10px 30px rgba(0,0,0,0.12);
  }
  .card--logo { left: 90px; top: 90px; }
  .card--contact { left: 510px; top: 560px; }

  .brand {
    position: absolute;
    display: flex;
    align-items: center;
    gap: 16px;
  }
  .brand__dot {
    width: 34px; height: 34px;
    border-radius: 50%;
    background: var(--orange-soft);
    flex: none;
  }
  .brand__name {
    font-family: "Montserrat", Arial, sans-serif;
    font-weight: 600;
    font-size: 38px;
    line-height: 1.05;
    color: var(--slate);
    letter-spacing: 0.3px;
  }
  .card--logo .brand { left: 70px; top: 110px; }
  .card--contact .brand { left: 60px; top: 48px; }

  .rule { position: absolute; height: 4px; background: var(--orange); }
  .rule--top { left: 420px; right: 0; top: 170px; }
  .rule--bottom { left: 0; width: 260px; top: 295px; }

  .web {
    position: absolute;
    font-size: 15px;
    color: var(--grey-text);
    letter-spacing: 1px;
  }
  .web em { font-style: normal; color: var(--orange); }
  .card--logo .web { left: 280px; top: 284px; }

  .contact-list {
    position: absolute;
    right: 34px; top: 120px;
    list-style: none;
    font-size: 15px;
    color: var(--grey-text);
    letter-spacing: 0.5px;
  }
  .contact-list li { display: flex; justify-content: flex-end; align-items: center; gap: 12px; height: 24px; }
  .contact-list svg { width: 14px; height: 14px; fill: var(--red); }

  .divider { position: absolute; left: 40px; right: 24px; top: 182px; height: 2px; background: var(--red); }

  .person { position: absolute; left: 40px; top: 196px; }
  .person__name {
    font-family: "Montserrat", Arial, sans-serif;
    font-weight: 700; font-size: 17px; color: var(--red); letter-spacing: 0.3px;
  }
  .person__role {
    font-family: "Montserrat", Arial, sans-serif;
    font-weight: 600; font-size: 14px; color: var(--orange); letter-spacing: 0.5px;
  }

  .address-band {
    position: absolute; left: 210px; right: 0; top: 198px; height: 38px;
    background: var(--orange);
    color: #fff; font-size: 15px; letter-spacing: 1px;
    display: flex; align-items: center; padding-left: 24px;
  }
  .card--contact .web { left: 300px; top: 250px; }
  .footer-band { position: absolute; left: 0; right: 0; bottom: 0; height: 34px; background: var(--orange); }
</style>
</head>
<body>
  <section class="card card--logo" aria-label="Card logo side">
    <div class="brand">
      <span class="brand__dot"></span>
      <span class="brand__name">Steered by Tallies</span>
    </div>
    <div class="rule rule--top"></div>
    <p class="web">www.<em>yoursitename</em>.com</p>
    <div class="rule rule--bottom"></div>
  </section>

  <section class="card card--contact" aria-label="Card contact side">
    <div class="brand">
      <span class="brand__dot"></span>
      <span class="brand__name">Steered by Tallies</span>
    </div>
    <ul class="contact-list">
      <li>000 000 0000
        <svg viewBox="0 0 24 24" aria-hidden="true"><path d="M6.6 10.8a15 15 0 0 0 6.6 6.6l2.2-2.2c.3-.3.7-.4 1-.2 1.1.4 2.3.6 3.6.6.6 0 1 .4 1 1V20c0 .6-.4 1-1 1A17 17 0 0 1 3 4c0-.6.4-1 1-1h3.5c.6 0 1 .4 1 1 0 1.3.2 2.5.6 3.6.1.3 0 .7-.2 1z"/></svg>
      </li>
      <li>info@yourmail.com
        <svg viewBox="0 0 24 24" aria-hidden="true"><path d="M2 5h20v14H2z M3 6l9 7 9-7" stroke="#fff" stroke-width="1.5"/></svg>
      </li>
    </ul>
    <div class="divider"></div>
    <div class="person">
      <p class="person__name">DANA WHITLOCK</p>
      <p class="person__role">FOUNDER</p>
    </div>
    <div class="address-band">your street address, suite-123, country-1230</div>
    <p class="web">www.<em>yoursite</em>.com</p>
    <div class="footer-band"></div>
  </section>
</body>
</html>
```